Real Estate 2015 sold listings postcard

Real estate. I want one side to list 2015 sales. Mailing side with additional information. I am including a "concept" but it needs to be professionalized... Feel free to change color, fonts, layout, add watermark, whatever you think will work. Text on backside may be tweaked. I do want postcards addressed. How do i send mailing list or does Kestro mail do that part?

NOTE: Postcard should be 8.5 x 5.5 inches.
Updates

postcard should be 8.5" x 5.5" size

Target Market(s)

Home owners who may want to sell

Industry/Entity Type

Real Estate Agent

Requirements
Must have
• The sold information and contact oinformation I have provided
Nice to have
• Watermark with my initials

```html
<!DOCTYPE html>
<html lang="en">
<head>
<meta charset="utf-8">
<title>Best Months to Sell – Postcard</title>
<link rel="stylesheet" href="https://fonts.googleapis.com/css2?family=Lato:wght@300;400;700;900&display=swap">
<style>
  :root {
    --red: #e5404a;
    --red-deep: #b72a35;
    --red-band: #9e2630;
    --text-red: #a8242e;
    --gold: #d9a72b;
    --gold-dark: #b98c1c;
    --ink: #2b2b2b;
    --paper: #ffffff;
    --paper-shade: #ececec;
  }
  html, body { margin: 0; padding: 0; overflow: hidden; background: var(--paper); }
  .postcard {
    position: relative;
    width: 1200px; height: 777px;
    overflow: hidden;
    font-family: 'Lato', sans-serif;
    background: radial-gradient(ellipse at 75% 45%, var(--paper) 40%, var(--paper-shade) 100%);
  }
  .backdrop { position: absolute; inset: 0; }
  .headline {
    position: absolute; left: 40px; top: 22px; margin: 0;
    color: var(--paper); font-weight: 300; font-size: 42px; line-height: 52px;
  }
  .headline .lead { font-size: 52px; display: block; line-height: 60px; }
  .headline strong { font-weight: 900; }
  .tab-offers {
    position: absolute; left: 150px; top: 214px;
    color: var(--text-red); font-weight: 900; font-size: 35px; line-height: 40px;
  }
  .box-prices {
    position: absolute; left: 52px; top: 270px; width: 272px; height: 62px;
    border-radius: 0 0 18px 18px; background: var(--red-deep);
    color: var(--paper); font-weight: 900; font-size: 34px;
    display: flex; align-items: center; justify-content: center;
  }
  .reach {
    position: absolute; right: 616px; top: 258px; margin: 0; text-align: right;
    color: var(--text-red); font-size: 24px; line-height: 29px;
  }
  .dont-wait {
    position: absolute; left: 76px; top: 340px; margin: 0;
    color: var(--text-red); font-weight: 300; font-size: 39px; line-height: 48px;
  }
  .cta {
    position: absolute; left: 0; top: 394px; width: 498px; height: 48px;
    background: var(--gold); color: var(--paper);
    font-weight: 900; font-size: 27px; line-height: 48px; padding-left: 40px; box-sizing: border-box;
  }
  .cta-tail { position: absolute; left: 474px; top: 410px; }
  .body-copy {
    position: absolute; left: 40px; top: 470px; width: 544px;
    color: var(--ink); font-size: 17px; line-height: 22px; text-align: justify;
    letter-spacing: -0.25px; word-spacing: -0.5px;
  }
  .body-copy p { margin: 0 0 7px; }
  .agent-photo {
    position: absolute; left: 762px; top: 34px; width: 150px; height: 150px;
    border-radius: 50%; border: 3px solid var(--paper);
    background: radial-gradient(circle at 50% 40%, #c9a08a 0 25%, #3c4e52 60%, #2c3a3e 100%);
    box-shadow: 0 2px 6px rgba(0,0,0,.25);
  }
  .agent { position: absolute; left: 924px; top: 0; width: 186px; height: 220px; text-align: center; }
  .agent > * { position: absolute; left: 0; right: 0; margin: 0; white-space: nowrap; }
  .agent-name { top: 41px; color: var(--paper); font-weight: 900; font-size: 21px; line-height: 24px; }
  .agent-license { top: 78px; color: var(--paper); font-weight: 300; font-size: 16px; line-height: 20px; }
  .agent-phone { top: 124px; color: var(--text-red); font-weight: 300; font-size: 28px; line-height: 34px; }
  .agent-email { top: 158px; color: var(--text-red); font-size: 19px; line-height: 22px; }
  .agent-web {
    top: 184px; left: 5px; right: 5px; height: 22px; line-height: 22px;
    border-radius: 11px; background: var(--gold); color: var(--paper); font-weight: 700; font-size: 17px;
  }
</style>
</head>
<body>
<div class="postcard">
  <svg class="backdrop" width="1200" height="777" viewBox="0 0 1200 777">
    <defs>
      <linearGradient id="redWash" x1="0" y1="0" x2="1" y2="0">
        <stop offset="0" stop-color="#d93640"/>
        <stop offset="0.5" stop-color="#f0545a"/>
        <stop offset="1" stop-color="#e23d46"/>
      </linearGradient>
    </defs>
    <path class="wave-band" d="M0,200 C110,245 250,268 400,252 C580,230 740,134 880,96 C960,74 1080,62 1200,74 V172 C1150,135 1080,110 960,110 C800,112 640,230 420,272 C260,298 110,272 0,214 Z" fill="var(--red-band)"/>
    <path class="wave-main" d="M0,0 H1200 V74 C1080,62 960,74 880,96 C740,134 580,230 400,252 C250,268 110,245 0,200 Z" fill="url(#redWash)"/>
    <path class="offers-tab" d="M100,262 C125,262 130,200 160,200 H330 C360,200 365,250 385,252 C300,268 200,270 100,262 Z" fill="var(--paper)"/>
  </svg>

  <h1 class="headline">
    <span class="lead">Traditionally</span>
    <strong>FEB</strong> through <strong>APRIL</strong><br>
    are the <strong>best months to sell</strong>
  </h1>

  <div class="tab-offers">Most Offers</div>
  <div class="box-prices">Highest Prices</div>

  <p class="reach">Our Listings are<br>advertised Locally and<br>in 40 countries!!</p>
  <p class="dont-wait">Don't Wait...</p>

  <div class="cta">Call Now for a Private Consultation!</div>
  <svg class="cta-tail" width="58" height="48" viewBox="0 0 58 48">
    <polygon points="24,0 58,0 40,28 58,48 0,48 24,32" fill="var(--gold)"/>
    <polygon points="0,48 24,32 24,36" fill="var(--gold-dark)"/>
  </svg>

  <div class="body-copy">
    <p>Our market continues to be strong, which reflects both our vibrant and growing local economy and our seemingly chronic shortage of inventory. As long as those conditions continue, our market values will remain high. That is good news to sellers who may want to down-size or move to a different area for a new job, or maybe to be closer to family.</p>
    <p>I am an Harbor Lane Realtors certified Relocation Specialist, and, as such, I can connect you with experienced and professional real estate agent anywhere in the country and in most countries around the world. We can co-ordinate your transactions at both ends, making your transition as seamless as possible. If you are planning a move, across the street or across the county, call me now for a confidential consultation.</p>
  </div>

  <div class="agent-photo" role="img" aria-label="Portrait photo of the agent"></div>
  <div class="agent">
    <p class="agent-name">DANA WHITFIELD</p>
    <p class="agent-license">License : #01482357</p>
    <p class="agent-phone">650-555-0148</p>
    <p class="agent-email">dwhitfield@hlr.com</p>
    <span class="agent-web">www.DWhitfield.com</span>
  </div>
</div>
</body>
</html>
```